International Railway Company Needs a Brochure - KVE Steady & Sure for Railway

We need a brochure for an International Company based in Italy called 'KVE'. We develop innovative instruments used in Railway monitoring for diagnostic and maintenance. Our main product is Track Geometry Measurement System (TGMS) - TGMS measuring the track geometry is composed by two profile measurement instruments (left and right) and one inertial pack. All these instruments are installed on a single rigid rod, mounted on a bogie All our products are based on Laser Triangulation Method.
We appreciate to see designs that use color blue but is not required.
The final design should communicate financial safety and growth. Also The final design should communicate our motto 'Steady & Sure'.
We'll send you our Company Logo, photos and contents. We are open to any suggestions.

Our web site is http://www.kvepralto.example/home.html
Updates

We are launching the contest for KVE new logo. It will be finished in 2/5 days. Thanks for your work.

 

Target Market(s)

Our main customers are International Railway Companies (LUVR-France, HT-Germany, OKP-Italy, ZWN-Switzerland) but also private companies.
Please see our competitors brochure in file attached "PXC Track Measuring Systems_EN_v6.pdf"

Industry/Entity Type

Financial

Requirements
Must have
• The brochure must have 6 pages A4 format like the example file PXC Track Measuring Systems_EN_v6

Page 1: Cover Page - KVE Synthesis
Page 2: Synthesis of the following products with one image for each

TMS
TGMS
RPMS
TRMS
TVS
DV

Page 3: TGMS details
Page 4: TMS and RPMS details
Page 5: TRMS and TVS and DV details
Page 6: Contacts

The text is not important. We can add it in a second time.

The file 115643_2387209_226909_vector is Company Logo file.
The file Final_KVE source logo1-bw is "family" Product logo.

Please feel free to change color at both logo if you need to do it or make it trasparent.
Should not have
• In the final brochure we don't want to see our VAT/TVA/IVA

```html
<!DOCTYPE html>
<html lang="en">
<head>
<meta charset="utf-8">
<title>KVE – Product Spread</title>
<link rel="stylesheet" href="https://fonts.googleapis.com/css2?family=Source+Sans+3:wght@700&family=Arimo:ital,wght@0,400;1,400&display=swap">
<style>
  :root {
    --backdrop: #e4e4e4;
    --paper: #f1f1f1;
    --paper-shade: #dcdcdc;
    --label-bg: #0b0b0b;
    --accent: #e2581f;
    --body-text: #2b2b2b;
    --rule: #1a1a1a;
    --chart-teal: #3cc6c9;
    --chart-green: #3a9a3a;
    --chart-orange: #e38b2c;
    --chart-blue: #2a3fa8;
    --chart-frame: #a8a8a8;
  }
  * { box-sizing: border-box; margin: 0; padding: 0; }
  html, body { width: 1200px; height: 1000px; overflow: hidden; }
  body { background: var(--backdrop); position: relative; font-family: "Arimo", Arial, sans-serif; }

  .spread { position: absolute; left: 90px; top: 123px; width: 1011px; height: 717px; }
  .page { position: absolute; top: 0; height: 717px; overflow: hidden; }
  .page--left { left: 0; width: 507px; background: linear-gradient(90deg, var(--paper) 0%, var(--paper) 82%, var(--paper-shade) 100%); }
  .page--right { left: 507px; width: 504px; background: linear-gradient(90deg, var(--paper-shade) 0%, var(--paper) 10%, var(--paper) 100%); }

  .label { position: absolute; background: var(--label-bg); color: var(--accent);
    font-family: "Source Sans 3", Arial, sans-serif; font-weight: 700; font-size: 23px; line-height: 1;
    display: flex; align-items: flex-end; padding: 0 0 12px 30px; }

  .copy { position: absolute; font-size: 10px; line-height: 11.6px; color: var(--body-text); }
  .copy span { display: block; height: 11.6px; white-space: nowrap; overflow: hidden; }
  .copy .gap { display: inline-block; width: 8px; }

  .photo { position: absolute; }
  .photo--undercar { left: 117px; top: 417px; width: 390px; height: 300px;
    background:
      radial-gradient(ellipse 40% 30% at 55% 40%, rgba(120,100,85,.55), transparent 70%),
      radial-gradient(ellipse 30% 14% at 45% 88%, rgba(190,170,60,.55), transparent 70%),
      linear-gradient(180deg, #5a4b3e 0%, #3b322b 45%, #2e2823 70%, #6f675d 100%); }
  .photo--wayside { left: 263px; top: 0; width: 241px; height: 322px;
    background:
      radial-gradient(ellipse 45% 50% at 78% 30%, rgba(60,60,58,.85), transparent 75%),
      linear-gradient(90deg, transparent 85%, rgba(200,140,40,.35) 100%),
      linear-gradient(180deg, #d7dcd6 0%, #9aa592 28%, #6b6c66 55%, #3e3d39 100%); }
  .photo--joint { left: 263px; top: 335px; width: 241px; height: 192px;
    background: linear-gradient(90deg, #6e4f3f 0%, #8c6a55 25%, #c9c6c1 42%, #a9a5a0 55%, #8c6a55 72%, #6e4f3f 100%); }
  .photo--platform { left: 0; top: 619px; width: 333px; height: 70px;
    background:
      linear-gradient(180deg, transparent 60%, rgba(220,170,40,.35) 100%),
      linear-gradient(90deg, #9c8b76 0%, #b29f86 35%, #8f8b86 55%, #7a746c 80%, #5f5952 100%); }
  .photo--yard { left: 345px; top: 539px; width: 159px; height: 178px;
    background:
      radial-gradient(ellipse 35% 45% at 50% 90%, rgba(120,110,100,.7), transparent 75%),
      linear-gradient(180deg, #dfe4ea 0%, #c3cbd3 22%, #8f8378 45%, #6a5f55 75%, #4d4640 100%); }

  .copy-panel { position: absolute; background: var(--paper); }
  .copy-panel--rpms { left: 0; top: 499px; width: 270px; height: 111px; border-radius: 0 16px 16px 0; }
  .copy-panel--tvs { left: 0; top: 419px; width: 343px; height: 114px; }

  .chart { position: absolute; left: 162px; top: 188px; }

  .brand-block { position: absolute; left: 0; top: 651px; width: 117px; height: 66px; background: var(--label-bg);
    display: flex; flex-direction: column; align-items: center; justify-content: center; gap: 6px; }
  .brand-mark { width: 14px; height: 14px; background: #ffffff; }
  .brand-name { color: #ffffff; font-family: "Source Sans 3", Arial, sans-serif; font-weight: 700; font-size: 15px; letter-spacing: 1px; line-height: 1; }

  .rule { position: absolute; left: 0; top: 698px; width: 338px; height: 2px; background: var(--rule); }
  .web { position: absolute; left: 352px; top: 692px; color: #ffffff; font-style: italic; font-size: 12px; }
</style>
</head>
<body>
<div class="spread">
  <section class="page page--left">
    <div class="label" style="left:0;top:0;width:117px;height:77px;">TMS</div>
    <div class="copy" style="left:18px;top:93px;width:380px;">
      <span>xxxxxxxxxxxxxxxxxxxxxxxxxxxxxxxxxxxxxxxxxxxxxxxxxxxxxxxxxxxxxxxxxxxxxxxxxxxxxxxx</span>
      <span>xxxxxxxxxxxxxxxxxxxxxxxxxxxxxxxxxxxxxxxxxxxxxxxxxxxxxxxxxxxxxxxxxxxxxxxxxxxxxxxx</span>
      <span>xxxxxxxxxxxxxxxxxxxxxxxxxxxxxxxxxxxxxxxxxxxxxxxxxxxxxxxxxxxxxxxxxxxxxxxxxxxxxxxx</span>
      <span>xxxxxxxxxxxxxxxxxxxxxxxxxxxxxxxxxxxxxxx<i class="gap"></i>xxxxxxxxxxxxxxxxxxxxxxxxxxxxxxxxxxxxxxxx</span>
      <span>xxxxxxxxxxxxxxxxxxxxxxxxxxxxxxxxxxxxxxxxxxxxxxxxxxxxxxxxxxxxxxxxxxxxxxxxxxxxxxxx</span>
      <span>xxxxxxxxxxxxxxxxxxxxxxxxxxxxxxxxxxxxxxxxxxxxxxxxxxxxxxxxxxxxxxxxxxxxxxxxxxxxxxxx</span>
      <span>xxxxxxxxxxxxxxxxxxxxxxxxxxxxxxxxxxxxxxxxxxxxxxxxxxxxxxxxxxxxxxxxxxxxxxxxxxxxxxxx</span>
    </div>
    <div class="copy" style="left:18px;top:179px;width:130px;">
      <span>xxxxxxxxxxxxxxxxxxxxxxxxxxxxxx</span>
      <span>xxxxxxxxxxxxxxxxxxxxxxxxxxxxxx</span>
      <span>xxxxxxxxxxxxxxxxxxxxxxxxxxxxxx</span>
      <span>xxxxxxx<i class="gap"></i>xxxxxxxxxxxxxxxxxxxxxx</span>
      <span>xxxxxxxxxxxxxxxxxxxxxxxxxxxxxx</span>
      <span>xxxxxxxxxxxxxxxxxxxxxxxxxxxxxx</span>
      <span>xxxxxxxxxxxxxxxxxxxxxxxxxxxxxx</span>
      <span>xxxxxxxxxxxxxxxxxxxxxxxxxxxxxx</span>
      <span>xxxxxxxxxxxxxxxxxxxxxxxxxxxxxx</span>
      <span>xxxxxxxxxxxxxxxxxxxxxxxxxxxxxx</span>
      <span>xxxxxxxxxxxxxxxxxxxxxxxxxxxxxx</span>
      <span>xxxxxxxxxxxxxxxxxxxxxxxxxxxxxx</span>
      <span>xxxxxxxxxxxxxxxxxxxxxxxxxxxxxx</span>
      <span>xxxxxxxxxxxxxxxxxxxxxxxxxxxxxx</span>
      <span>xxxxxxxxxxxxxxxxxxxxxxxxxxxxxx</span>
      <span>xxxxxxxxxxxxxxxxxxxxxxxxxxxxxx</span>
    </div>

    <svg class="chart" width="302" height="200" viewBox="0 0 302 200" role="img" aria-label="Track measurement line chart with six stacked panels">
      <g fill="#ffffff" stroke="var(--chart-frame)" stroke-width="0.6">
        <rect x="10" y="2" width="290" height="26"/><rect x="10" y="34" width="290" height="26"/>
        <rect x="10" y="66" width="290" height="26"/><rect x="10" y="96" width="290" height="26"/>
        <rect x="10" y="128" width="290" height="30"/><rect x="10" y="162" width="290" height="30"/>
      </g>
      <g fill="none" stroke-width="1.3">
        <polyline stroke="var(--chart-teal)" points="10,8 80,7 150,9 220,7 300,8"/>
        <polyline stroke="var(--chart-green)" points="10,12 300,11"/>
        <path stroke="var(--chart-orange)" d="M30 16 q15 10 30 0 M120 16 q15 10 30 0 M200 16 q15 10 30 0"/>
        <polyline stroke="var(--chart-green)" points="10,44 300,43"/>
        <polyline stroke="var(--chart-teal)" points="10,50 300,50"/>
        <path stroke="var(--chart-orange)" d="M40 40 q10 10 20 0 M110 40 q10 10 20 0 M180 40 q10 10 20 0 M250 40 q10 10 20 0"/>
        <polyline stroke="var(--chart-blue)" points="10,80 30,79 32,70 34,82 90,80 140,79 150,72 152,82 220,80 300,79"/>
        <polyline stroke="var(--chart-orange)" points="10,110 40,107 60,112 90,108 120,111 150,106 180,112 210,108 240,111 270,107 300,110"/>
        <polyline stroke="var(--chart-teal)" points="10,108 40,111 60,106 90,110 120,107 150,112 180,107 210,111 240,106 270,110 300,108"/>
        <path stroke="var(--chart-blue)" d="M25 135 q10 20 20 0 M90 135 q10 20 20 0 M140 138 q10 15 20 0 M230 135 q10 20 20 0 M275 135 q10 20 20 0"/>
        <path stroke="var(--chart-green)" d="M25 170 q10 18 20 0 M90 172 q12 16 24 0 M230 170 q10 18 20 0 M275 170 q10 18 20 0"/>
        <path stroke="var(--chart-orange)" d="M30 180 q8 8 16 0 M150 178 q8 8 16 0 M240 180 q8 8 16 0"/>
      </g>
    </svg>

    <div class="photo photo--undercar" role="img" aria-label="Photo of measuring unit mounted under a rail vehicle bogie"></div>
    <div class="label" style="left:0;top:419px;width:117px;height:75px;">RPMS</div>
    <div class="copy-panel copy-panel--rpms"></div>
    <div class="copy" style="left:18px;top:505px;width:240px;">
      <span>xxxxxxxxxxxxxxxxxxxxxxxxxxxxxxxxxxxxxxxxxxxxxxxxxxxx</span>
      <span>xxxxxxxxxxxxxxxxxxxxxxxxxxxxxxxxxxxxxxxxxxxxxxxxxxxx</span>
      <span>xxxxxxxxxxxxxxxxxxxxxxxxxxxxxxxxxxxxxxxxxxxxxxxxxxxx</span>
      <span>xxxxxxxxxxxxxxxxxxxxxxxxxxxxxxxxxxxxxxxxxxxxxxxxxxxx</span>
      <span>xxxxxxxxxxxxxxxxxxxxxxxxxxxxxxxxxxxxxxxxxxxxxxxxxxxx</span>
      <span>xxxxxxxxxxxxxxxxxxxxxxxxxxxxxxxxxxxxxxxxxxxxxxxxxxxx</span>
      <span>xxxxxxxxxxxxxxxxxxxxxxxxxxx<i class="gap"></i>xxxxxxxxxxxxxxxxxxxxxxx</span>
      <span>xxxxxxxxxxxxxxxxxxxxxxxxxxxxxxxxxxxxxxxxxxxxxxxxxxxx</span>
    </div>
    <div class="brand-block"><span class="brand-mark"></span><span class="brand-name">KVE</span></div>
  </section>

  <section class="page page--right">
    <div class="label" style="left:0;top:0;width:115px;height:77px;">TRMS</div>
    <div class="copy" style="left:23px;top:85px;width:225px;">
      <span>xxxxxxxxxxxxxxxxxxxxxxxxxxxxxxxxxxxxxxxxxxxxxxxxxx</span>
      <span>xxxxxxxxxxxxxxxxxxxxxxxxxxxxxxxxxxxxxxxxxxxxxxxxxx</span>
      <span>xxxxxxxxxxxxxxxxxxxxxxxxxxxxxxxxxxxxxxxxxxxxxxxxxx</span>
      <span>xxxxxxxxxxxxxxxxxxxxxxxxxxxxxxxxxxxxxxxxxxxxxxxxxx</span>
      <span>xxxxxxxxxxxxxxxxxxxxxxxxxxxxxxxxxxxxxxxxxxxxxxxxxx</span>
      <span>xxxxxxxxxxxxxxxxxxxxxxxxxxxxxxxxxxxxxxxxxxxxxxxxxx</span>
      <span>xxxxxxxxxxxxxxxxxxxxxxxxxxxxxxxxxxxxxxxxxxxxxxxxxx</span>
      <span>xxxxxxxxxxxxxxxxxxxxxxxxxxxxxxxxxxxxxxxxxxxxxxxxxx</span>
      <span>xx<i class="gap"></i>xxxxxxxxxxxxxxxxxxxxxxxxxxxxxxxxxxxxxxxxxxxxxx</span>
      <span>xxxxxxxxxxxxxxxxxxxxxxxxxxxxxxxxxxxxxxxxxxxxxxxxxx</span>
      <span>xxxxxxxxxxxxxxxxxxxxxxxxxxxxxxxxxxxxxxxxxxxxxxxxxx</span>
      <span>xxxxxxxxxxxxxxxxxxxxxxxxxxxxxxxxxxxxxxxxxxxxxxxxxx</span>
      <span>xxxxxxxxxxxxxxxxxxxxxxxxxxxxxxxxxxxxxxxxxxxxxxxxxx</span>
      <span>xxxxxxxxxxxxxxxxxxxxxxxxxxxxxxxxxxxxxxxxxxxxxxxxxx</span>
      <span>xxxxxxxxxxxxxxxxxxxxxxxxxxxxxxxxxxxxxxxxxxxxxxxxxx</span>
      <span>xxxxxxxxxxxxxxxxxxxxxxxxxxxxxxxxxxxxxxxxxxxxxxxxxx</span>
      <span>xx<i class="gap"></i>xxxxxxxxxxxxxxxxxxxxxxxxxxxxxxxxxxxxxxxxxxxxxx</span>
      <span>xxxxxxxxxxxxxxxxxxxxxxxxxxxxxxxxxxxxxxxxxxxxxxxxxx</span>
      <span>xxxxxxxxxxxxxxxxxxxxxxxxxxxxxxxxxxxxxxxxxxxxxxxxxx</span>
      <span>xxxxxxxxxxxxxxxxxxxxxxxxxxxxxxxxxxxxxxxxxxxxxxxxxx</span>
    </div>
    <div class="photo photo--wayside" role="img" aria-label="Photo of track recording equipment on a rail vehicle beside a platform"></div>

    <div class="label" style="left:0;top:334px;width:115px;height:75px;">TVS</div>
    <div class="photo photo--joint" role="img" aria-label="Close-up photo of a rail joint with bolts"></div>
    <div class="copy-panel copy-panel--tvs"></div>
    <div class="copy" style="left:23px;top:428px;width:310px;">
      <span>xxxxxxxxxxxxxxxxxxxxxxxxxxxxxxxxxxxxxxxxxxxxxxxxxxxxxxxxxxxxxxxxxx</span>
      <span>xxxxxxxxxxxxxxxxxxxxxxxxxxxxxxxxxxxxxxxxxxxxxxxxxxxxxxxxxxxxxxxxxx</span>
      <span>xxxxxxxxxxxxxxxxxxxxxxxxxxxxxxxxxxxxxxxxxxxxxxxxxxxxxxxxxxxxxxxxxx</span>
      <span>xxxxxxxxxxxxxxxxxxxxxxxxxxxxxxxxxxxxxxxxxxxxxxxxxxxxxxxxxxxxxxxxxx</span>
      <span>xxxxxxxxxxxxxxxxxxx<i class="gap"></i>xxxxxxxxxxxxxxxxxxxxxxxxxxxxxxxxxxxxxxxxxxxxx</span>
      <span>xxxxxxxxxxxxxxxxxxxxxxxxxxxxxxxxxxxxxxxxxxxxxxxxxxxxxxxxxxxxxxxxxx</span>
      <span>xxxxxxxxxxxxxxxxxxxxxxxxxxxxxxxxxxxxxxxxxxxxxxxxxxxxxxxxxxxxxxxxxx</span>
    </div>

    <div class="label" style="left:0;top:540px;width:115px;height:77px;">DV</div>
    <div class="copy" style="left:123px;top:542px;width:210px;">
      <span>xxxxxxxxxxxxxxxxxxxxxxxxxxxxxxxxxxxxxxxxxxxxxx</span>
      <span>xxxxxxxxxxxxxxxxxxxxxxxxxxxxxxxxxxxxxxxxxxxxxx</span>
      <span>xxxxxxxxxxxxxxxxxxxxxxxxxxxxxxxxxxxxxxxxxxxxxx</span>
      <span>xxxxxxxxxxxxxxxxxxxxxxxxxxxxxxxxxxxxxxxxxxxxxx</span>
      <span>xxxxxxxxxxxxxxxxxxxxxxxxxxxxxxxxxxxxxxxxxxxxxx</span>
    </div>
    <div class="photo photo--platform" role="img" aria-label="Photo of railway tracks at a station platform"></div>
    <div class="rule"></div>
    <div class="photo photo--yard" role="img" aria-label="Photo of a railway yard with tracks and a station building"></div>
    <span class="web">www.kvepralto.example</span>
  </section>
</div>
</body>
</html>
```